Harborline Auto LLC

Car Dealer Customer Service
Address: 2874 Cresthaven Road, Shelbyville, TN 37162
web: www.harborlineautoxq.net
email: harborlineautoxq@mailnest.example
Phone: (931) 555-0148
Phone: (629) 555-0173

```html
<!DOCTYPE html>
<html lang="en">
<head>
<meta charset="utf-8">
<title>Harborline Auto — Business Card</title>
<link rel="stylesheet" href="https://fonts.googleapis.com/css2?family=Montserrat:wght@400;700&display=swap">
<style>
  :root {
    --page-bg: #e9eaec;
    --card-white: #ffffff;
    --brand-blue: #2a93d0;
    --brand-navy: #1f72b0;
    --brand-yellow: #e9b143;
    --text-light: #ffffff;
  }
  * { margin: 0; padding: 0; box-sizing: border-box; }
  html, body {
    width: 1200px; height: 900px; overflow: hidden;
    background: var(--page-bg);
    font-family: "Montserrat", sans-serif;
  }
  .canvas { position: relative; width: 1200px; height: 900px; }
  .card {
    position: absolute; width: 660px; height: 380px;
    background: var(--card-white);
    box-shadow: 0 6px 18px rgba(0,0,0,0.12);
    overflow: hidden;
  }
  .card-front { left: 60px; top: 50px; }
  .card-back { left: 480px; top: 470px; }

  .brand { display: flex; align-items: center; gap: 16px; color: var(--brand-navy); }
  .brand-mark { border-radius: 50%; background: var(--brand-blue); flex: none; }
  .brand-name { font-weight: 700; text-transform: uppercase; letter-spacing: 0.02em; white-space: nowrap; }

  .card-front .brand {
    position: absolute; left: 50%; top: 50%; transform: translate(-50%, -50%);
  }
  .card-front .brand-mark { width: 58px; height: 58px; }
  .card-front .brand-name { font-size: 38px; }

  .back-art { position: absolute; inset: 0; }
  .card-back .brand { position: absolute; right: 34px; top: 62px; }
  .card-back .brand-mark { width: 40px; height: 40px; }
  .card-back .brand-name { font-size: 25px; }

  .contact {
    position: absolute; left: 40px; top: 150px;
    color: var(--text-light); font-size: 16px; line-height: 1.5;
    list-style: none;
  }
  .contact .role { margin-bottom: 0; }
  .contact .address { margin-bottom: 4px; }
  .contact-line { display: flex; align-items: center; gap: 10px; }
  .contact-icon { width: 18px; height: 18px; flex: none; }
</style>
</head>
<body>
<main class="canvas">

  <section class="card card-front" aria-label="Card front">
    <div class="brand">
      <span class="brand-mark"></span>
      <span class="brand-name">Harborline Auto</span>
    </div>
  </section>

  <section class="card card-back" aria-label="Card back">
    <svg class="back-art" viewBox="0 0 660 380" width="660" height="380" aria-hidden="true">
      <rect width="660" height="380" fill="var(--brand-blue)"/>
      <path d="M212,0 H660 V380 H568 C560,318 515,272 430,242 C318,202 226,142 212,0 Z" fill="#ffffff"/>
      <path d="M222,0 H244 C258,108 360,150 470,194 C560,230 604,292 596,350 C590,330 572,298 540,276 C505,254 470,244 430,230 C330,194 236,140 222,0 Z" fill="var(--brand-yellow)"/>
      <path d="M222,0 C236,140 330,194 430,230 C470,244 505,254 540,276 C572,298 590,330 596,350" fill="none" stroke="#ffffff" stroke-width="4"/>
    </svg>

    <div class="brand">
      <span class="brand-mark"></span>
      <span class="brand-name">Harborline Auto</span>
    </div>

    <ul class="contact">
      <li class="role">Car Dealer Customer Service</li>
      <li>2874 Cresthaven Road,</li>
      <li class="address">Shelbyville, TN 37162</li>
      <li class="contact-line">
        <svg class="contact-icon" viewBox="0 0 20 20" aria-label="Mobile phone"><path d="M5 2 L8 2 L9 6 L7 8 C8 11 10 13 12 13 L14 11 L18 12 L18 15 C18 17 16 18 14 18 C8 17 3 12 2 6 C2 4 3 2 5 2 Z" fill="var(--brand-yellow)"/></svg>
        <span>(931) 555-0148</span>
      </li>
      <li class="contact-line">
        <svg class="contact-icon" viewBox="0 0 20 20" aria-label="Telephone"><path d="M2 7 C6 3 14 3 18 7 L16 9 L13 8 L13 6 C11 5 9 5 7 6 L7 8 L4 9 Z" fill="var(--brand-yellow)"/><rect x="4" y="10" width="12" height="7" rx="1.5" fill="var(--brand-yellow)"/></svg>
        <span>(629) 555-0173</span>
      </li>
      <li class="contact-line">
        <svg class="contact-icon" viewBox="0 0 20 20" aria-label="Email"><rect x="2" y="5" width="16" height="11" rx="1" fill="var(--brand-yellow)"/><path d="M2.5 5.5 L10 11 L17.5 5.5" fill="none" stroke="var(--brand-blue)" stroke-width="1.5"/></svg>
        <span>harborlineautoxq@mailnest.example</span>
      </li>
      <li class="contact-line">
        <svg class="contact-icon" viewBox="0 0 20 20" aria-label="Website"><circle cx="10" cy="10" r="8" fill="var(--brand-yellow)"/><path d="M2 10 H18 M10 2 C6 6 6 14 10 18 M10 2 C14 6 14 14 10 18" fill="none" stroke="var(--brand-blue)" stroke-width="1.2"/></svg>
        <span>www.harborlineautoxq.net</span>
      </li>
    </ul>
  </section>

</main>
</body>
</html>
```